Coastline Premier Retreats Business Card Design

Design a business card for Coastline Premier Retreats. Look at the website for colors and reference. Card should have logo, name, title, office number, mobile number, email, URL and a tagline like, "Luxury Hotel & Resort Email Marketing" (This might change).

https://www.coastlinepremierretreats.example

The rest I will leave up to your imagination.

Contact Information for Business Card

Logo, name, title, office number, mobile number, email, URL and a tagline like, "Luxury Hotel & Resort Email Marketing" (This might change).

```html
<!DOCTYPE html>
<html lang="en">
<head>
<meta charset="utf-8">
<title>Coastline Premier Retreats – Business Card</title>
<link rel="stylesheet" href="https://fonts.googleapis.com/css2?family=Montserrat:wght@600;700;800&family=Open+Sans:wght@400;600&display=swap">
<style>
  :root {
    --stage: #232323;
    --orange: #f37421;
    --card-dark: #1c1d21;
    --layer-mid: #232428;
    --layer-top: #1f2024;
    --white: #ffffff;
    --soft-white: #e9e9ea;
  }
  * { box-sizing: border-box; margin: 0; padding: 0; }
  html, body { width: 1200px; height: 780px; overflow: hidden; }
  body {
    background: var(--stage);
    position: relative;
    font-family: "Open Sans", Arial, sans-serif;
  }
  .card {
    position: absolute;
    top: 80px;
    width: 354px;
    height: 620px;
    border-radius: 24px;
    overflow: hidden;
    box-shadow: 0 18px 40px rgba(0,0,0,0.55);
  }

  /* Front */
  .card-front { left: 190px; background: var(--orange); }
  .front-wordmark {
    position: absolute;
    left: 50%;
    top: 50%;
    width: 560px;
    transform: translate(-50%, -50%) rotate(-90deg);
    text-align: center;
    font-family: "Montserrat", Arial, sans-serif;
    font-weight: 800;
    font-size: 38px;
    line-height: 1.15;
    letter-spacing: 2px;
    color: var(--white);
    text-transform: uppercase;
  }

  /* Back */
  .card-back { left: 656px; background: var(--card-dark); }
  .back-layers { position: absolute; inset: 0; }
  .back-content { position: absolute; inset: 0; text-align: center; }
  .back-logo {
    position: absolute;
    top: 58px;
    left: 0; right: 0;
    display: flex;
    justify-content: center;
    align-items: center;
    gap: 10px;
  }
  .back-logo-mark { width: 14px; height: 14px; background: var(--orange); }
  .back-logo-name {
    font-family: "Montserrat", Arial, sans-serif;
    font-weight: 800;
    font-size: 17px;
    line-height: 1.2;
    letter-spacing: 1px;
    color: var(--white);
    text-transform: uppercase;
    text-align: left;
  }
  .person { position: absolute; top: 205px; left: 0; right: 0; }
  .person-name {
    font-family: "Montserrat", Arial, sans-serif;
    font-weight: 700;
    font-size: 30px;
    color: var(--white);
  }
  .person-name .first { color: var(--orange); }
  .person-title { font-size: 14px; color: var(--soft-white); margin-top: 2px; }
  .contact-icons {
    position: absolute; top: 290px; left: 0; right: 0;
    display: flex; justify-content: center; gap: 8px;
  }
  .contact-icons svg { width: 22px; height: 22px; }
  .contact-list {
    position: absolute; top: 324px; left: 0; right: 0;
    list-style: none;
    font-size: 13.5px;
    line-height: 1.55;
    color: var(--white);
  }
  .tagline {
    position: absolute; bottom: 56px; left: 0; right: 0;
    font-size: 15px;
    font-weight: 600;
    line-height: 1.4;
    color: var(--orange);
  }
</style>
</head>
<body>

  <section class="card card-front" aria-label="Card front">
    <div class="front-wordmark">Coastline<br>Premier Retreats</div>
  </section>

  <section class="card card-back" aria-label="Card back">
    <svg class="back-layers" viewBox="0 0 354 620" preserveAspectRatio="none" aria-hidden="true">
      <defs>
        <filter id="layer-shadow" x="-10%" y="-10%" width="120%" height="130%">
          <feDropShadow dx="0" dy="6" stdDeviation="8" flood-color="#000" flood-opacity="0.45"/>
        </filter>
      </defs>
      <path d="M0 0 H354 V440 Q230 600 0 560 Z" fill="var(--layer-mid)" filter="url(#layer-shadow)"/>
      <path d="M0 0 H354 V380 Q250 500 0 455 Z" fill="var(--layer-top)" filter="url(#layer-shadow)"/>
    </svg>

    <div class="back-content">
      <div class="back-logo">
        <span class="back-logo-mark"></span>
        <span class="back-logo-name">Coastline<br>Premier Retreats</span>
      </div>

      <div class="person">
        <div class="person-name"><span class="first">Marina</span> Kovalek</div>
        <div class="person-title">Co-Founder</div>
      </div>

      <div class="contact-icons" aria-hidden="true">
        <svg viewBox="0 0 22 22"><circle cx="11" cy="11" r="11" fill="var(--orange)"/><path d="M7.5 6.5 l2 0 l1 2.5 l-1.2 1 a6 6 0 0 0 2.7 2.7 l1-1.2 l2.5 1 l0 2 a1 1 0 0 1 -1 1 a9 9 0 0 1 -8-8 a1 1 0 0 1 1-1z" fill="#fff"/></svg>
        <svg viewBox="0 0 22 22"><circle cx="11" cy="11" r="11" fill="var(--orange)"/><rect x="8" y="5.5" width="6" height="11" rx="1.2" fill="none" stroke="#fff" stroke-width="1.4"/></svg>
        <svg viewBox="0 0 22 22"><circle cx="11" cy="11" r="11" fill="var(--orange)"/><rect x="6" y="7.5" width="10" height="7" fill="none" stroke="#fff" stroke-width="1.3"/><path d="M6 7.5 l5 4 l5-4" fill="none" stroke="#fff" stroke-width="1.3"/></svg>
        <svg viewBox="0 0 22 22"><circle cx="11" cy="11" r="11" fill="var(--orange)"/><circle cx="11" cy="11" r="5.5" fill="none" stroke="#fff" stroke-width="1.3"/><path d="M5.5 11 H16.5 M11 5.5 Q8 11 11 16.5 M11 5.5 Q14 11 11 16.5" fill="none" stroke="#fff" stroke-width="1.1"/></svg>
      </div>

      <ul class="contact-list">
        <li>(555) 014-2758</li>
        <li>(555) 014-7777</li>
        <li>www.coastlinepremierretreats.example</li>
        <li>info@coastlinepremierretreats.example</li>
      </ul>

      <p class="tagline">Luxury Hotel &amp;<br>Resort Email Marketing</p>
    </div>
  </section>

</body>
</html>
```